Upscale business cards needed for Board of Directors

We need professional business cards created for members of our family business Board of Directors. We would like these relatively simple and straightforward, but also with a unique element to set them apart. Probably stick with neutral and simple colors - white, grey etc. We need space for the traditional elements, including name, title, address, email/phone number. And we will be creating several from this template so it needs to be template that is easy to switch information in and out of.
Business
See description

```html
<!DOCTYPE html>
<html lang="en">
<head>
<meta charset="utf-8">
<title>Keelstone Holdings – Business Card</title>
<link rel="stylesheet" href="https://fonts.googleapis.com/css2?family=Roboto:wght@400;500;700&display=swap">
<style>
  :root {
    --page-bg: #dcd9d5;
    --card-top: #eeeeec;
    --card-top-edge: #e2e2df;
    --gold-light: #c3a57c;
    --gold-dark: #8d7352;
    --band-top: #3b3a38;
    --band-bottom: #0f0f0f;
    --ink: #1b1b1b;
    --name-ink: #f6f1ea;
    --title-ink: #f1e8dc;
    --contact-ink: #e3ddd6;
    --address-ink: #c9ad86;
  }
  * { margin: 0; padding: 0; box-sizing: border-box; }
  html, body {
    width: 1200px; height: 969px; overflow: hidden;
    background: var(--page-bg);
    font-family: "Roboto", sans-serif;
  }
  .card {
    position: absolute; left: 100px; top: 200px;
    width: 1000px; height: 568px;
    background: linear-gradient(180deg, var(--card-top) 0%, var(--card-top-edge) 100%);
    box-shadow: 0 18px 40px rgba(0,0,0,0.18);
    overflow: hidden;
  }
  .card-bands { position: absolute; inset: 0; width: 1000px; height: 568px; }
  .brand {
    position: absolute; right: 66px; top: 118px;
    text-align: center; color: var(--ink);
    font-weight: 700; line-height: 1;
  }
  .brand-name { display: block; font-size: 70px; letter-spacing: 1px; }
  .brand-sub { display: block; font-size: 70px; letter-spacing: 1px; margin-top: 6px; }
  .holder { position: absolute; left: 64px; top: 288px; }
  .holder-name { font-size: 31px; font-weight: 500; color: var(--name-ink); }
  .holder-title { font-size: 25px; font-weight: 400; color: var(--title-ink); margin-top: 4px; }
  .contact-list { position: absolute; left: 64px; top: 424px; list-style: none; }
  .contact-item {
    display: flex; align-items: center; height: 38.5px;
    font-size: 24px; color: var(--contact-ink);
  }
  .contact-icon { width: 26px; height: 26px; margin-right: 24px; fill: var(--gold-light); }
  .address {
    position: absolute; right: 64px; top: 466px; text-align: right;
    font-size: 24px; line-height: 38.5px; color: var(--address-ink);
  }
</style>
</head>
<body>
  <article class="card">
    <svg class="card-bands" viewBox="0 0 1000 568" aria-hidden="true">
      <defs>
        <linearGradient id="goldFill" x1="0" y1="0" x2="1" y2="0">
          <stop offset="0" stop-color="var(--gold-dark)"/>
          <stop offset="0.5" stop-color="var(--gold-light)"/>
          <stop offset="1" stop-color="var(--gold-dark)"/>
        </linearGradient>
        <linearGradient id="bandFill" x1="0" y1="0" x2="0" y2="1">
          <stop offset="0" stop-color="var(--band-top)"/>
          <stop offset="1" stop-color="var(--band-bottom)"/>
        </linearGradient>
      </defs>
      <path d="M0 272 H336 L400 362 H1000 V378 H0 Z" fill="url(#goldFill)"/>
      <rect x="0" y="378" width="1000" height="190" fill="url(#bandFill)"/>
    </svg>

    <div class="brand">
      <span class="brand-name">KEELSTONE</span>
      <span class="brand-sub">HOLDINGS</span>
    </div>

    <div class="holder">
      <p class="holder-name">Martin Hale</p>
      <p class="holder-title">President</p>
    </div>

    <ul class="contact-list">
      <li class="contact-item">
        <svg class="contact-icon" viewBox="0 0 24 24" aria-hidden="true"><path d="M6.6 10.8a15 15 0 0 0 6.6 6.6l2.2-2.2a1 1 0 0 1 1-.25 11.4 11.4 0 0 0 3.6.57 1 1 0 0 1 1 1V20a1 1 0 0 1-1 1A17 17 0 0 1 3 4a1 1 0 0 1 1-1h3.5a1 1 0 0 1 1 1c0 1.25.2 2.45.57 3.57a1 1 0 0 1-.25 1Z"/></svg>
        555 0148 2290
      </li>
      <li class="contact-item">
        <svg class="contact-icon" viewBox="0 0 24 24" aria-hidden="true"><path d="M2 5h20v14H2Zm2 2v.6l8 5 8-5V7Z"/></svg>
        martin@keelstone.com
      </li>
      <li class="contact-item">
        <svg class="contact-icon" viewBox="0 0 24 24" aria-hidden="true"><circle cx="12" cy="12" r="10"/><path d="M2 12h20M12 2a15 15 0 0 1 0 20M12 2a15 15 0 0 0 0 20" stroke="var(--band-top)" stroke-width="1.6" fill="none"/></svg>
        www.keelstone.com
      </li>
    </ul>

    <address class="address" style="font-style:normal">
      412 Linden Crest Road<br>
      Maple Hollow, NY 10990
    </address>
  </article>
</body>
</html>
```